Provide bookkeeping and accounting services to small and growing businesses

We need website and logo design using the name Dornaby as the logo.
The target audience are small companies and startups who need:
1) Simple bookkeeping services
2) Accounting advice that only someone with many years of senior financial experience as a CPA can provide.

The services are provided by two individuals. each of whom specialize in one of the areas.

We want the website to be clean without a lot of visual distraction but don't know how to make a boring subject interesting. We believe our potential clients, small business owners, need to find what they want quickly and easily without a lot of verbiage or distractions.

We've attached a draft of the homepage and have completed the text on most of the other pages.

Target Market(s)

small and early stage growth companies in San Diego North County

Industry/Entity Type

Accounting

Number of Pages Required

1 page

Font styles to use
Sans Serif

Colors
86cfc6
33b8a4
85cae6

Requirements
Must have
• We need a design for the website homepage that includes the name Dornaby as the logo. Must include a design for the name.
• Must have color in teal or greenish blue.
Nice to have
• White background, clean, clear, uncluttered.
• We would like to use the design in a Theme on a WordPress website. Themes Paper Lantern and Quiet Harbour are appealing to us.
Should not have
• Moving pictures

```html
<!DOCTYPE html>
<html lang="en">
<head>
<meta charset="utf-8">
<title>Dornaby — Accounting and Bookkeeping</title>
<link href="https://fonts.googleapis.com/css2?family=Cinzel:wght@400&family=Open+Sans:wght@400;600&family=Raleway:wght@300&family=Roboto:wght@400&display=swap" rel="stylesheet">
<style>
  :root{
    --teal:#33b8a4;
    --teal-soft:#86cfc6;
    --teal-line:#6ccabf;
    --ink:#444;
    --body:#555;
    --nav:#666;
    --white:#fff;
  }
  *{box-sizing:border-box;margin:0;padding:0}
  html,body{width:1200px;height:1153px;overflow:hidden;background:var(--white)}
  body{font-family:"Open Sans",sans-serif;color:var(--body);position:relative}
  .topbar{position:absolute;top:0;left:0;width:1200px;height:2px;background:var(--teal)}
  .site-header{position:absolute;top:2px;left:0;width:1200px;height:77px;border-bottom:1px solid #e2e2e2}
  .brand{position:absolute;left:97px;top:16px;color:var(--teal);font-family:"Open Sans",sans-serif;font-weight:600}
  .brand-name{font-size:28px;line-height:32px;letter-spacing:.5px}
  .brand-tag{font-size:10px;line-height:14px;letter-spacing:.6px;margin-top:2px}
  .main-nav{position:absolute;top:30px;right:97px;display:flex;gap:50px;font-size:14px;color:var(--nav)}
  .main-nav .current{color:var(--teal)}
  .hero{position:absolute;top:79px;left:0;width:1200px;height:375px;background:linear-gradient(120deg,#4b4f55 0%,#8c8f93 35%,#c4c6c9 55%,#7b7c7f 80%,#3e4044 100%)}
  .hero-panel{position:absolute;left:135px;top:105px;width:612px;height:177px;background:rgba(51,184,164,.82);color:var(--white);font-family:"Raleway",sans-serif;font-weight:300;padding:20px 0 0 32px}
  .hero-title{font-size:48px;line-height:54px}
  .hero-text{font-size:25px;line-height:31px;margin-top:4px;padding-left:4px}
  .hero-shadow{position:absolute;top:454px;left:0;width:1200px;height:30px;background:radial-gradient(ellipse 50% 100% at 50% 0,rgba(0,0,0,.12),rgba(0,0,0,0))}
  .welcome{position:absolute;top:494px;left:0;width:1200px;text-align:center}
  .welcome h1{font-family:"Cinzel",serif;font-weight:400;font-size:32px;color:var(--ink);letter-spacing:1px;line-height:40px}
  .welcome h2{font-family:"Cinzel",serif;font-weight:400;font-size:23px;color:var(--teal);letter-spacing:1px;line-height:30px;margin-top:-2px}
  .welcome p{width:740px;margin:8px auto 0;font-size:12px;line-height:20.5px}
  .services{position:absolute;top:650px;left:99px;display:flex;gap:42px}
  .service{width:306px;text-align:center}
  .service-photo{width:306px;height:190px;box-shadow:0 4px 4px -3px rgba(0,0,0,.25)}
  .service h3{font-size:17px;font-weight:600;color:var(--ink);margin-top:26px;line-height:22px}
  .service.featured h3{color:var(--teal)}
  .service p{font-size:12px;line-height:20.5px;margin-top:6px;padding:0}
  .service-rule{height:2.5px;background:var(--teal-line);margin-top:24px}
  .service.featured .service-rule{background:var(--teal)}
  .site-footer{position:absolute;top:1038px;left:0;width:1200px;height:115px;background:var(--teal);text-align:center;color:var(--white)}
  .social{display:flex;justify-content:center;gap:25px;margin-top:32px}
  .social span{width:18px;height:18px;border-radius:50%;background:var(--white)}
  .copyright{font-family:"Roboto",sans-serif;font-size:14px;margin-top:16px}
</style>
</head>
<body>
  <div class="topbar"></div>
  <header class="site-header">
    <div class="brand">
      <div class="brand-name">Dornaby</div>
      <div class="brand-tag">Accounting and Bookkeeping</div>
    </div>
    <nav class="main-nav">
      <span class="current">Home</span><span>About Us</span><span>Services</span><span>Experience</span><span>Resources</span><span>Contact Us</span>
    </nav>
  </header>

  <section class="hero" role="img" aria-label="Photo of two people reviewing financial charts at a desk with a pen">
    <div class="hero-panel">
      <div class="hero-title">DORNABY</div>
      <div class="hero-text">We simple book keeping services, financial<br>&amp; accounting advice for small start up companies.</div>
    </div>
  </section>
  <div class="hero-shadow"></div>

  <section class="welcome">
    <h1>Welcome To Dornaby</h1>
    <h2>We are Accounting and Bookkeeping</h2>
    <p>Dornaby offers a flexible range of accounting and bookkeeping services and support for small and growing organizations in San Diego North County. We provide bookkeeping services specializing in LedgerBooks® at your offices or remotely from ours.</p>
  </section>

  <section class="services">
    <article class="service featured">
      <div class="service-photo" role="img" aria-label="Photo of a hand browsing through office binders" style="background:linear-gradient(160deg,#e9d3dc,#dcdcdc 55%,#b9bcbf)"></div>
      <h3>BOOKKEEPING SERVICES</h3>
      <p>It is a long established fact that a reader will be distracted by the readable content of a page when looking at its layout. The point of using Lorem</p>
      <div class="service-rule"></div>
    </article>
    <article class="service">
      <div class="service-photo" role="img" aria-label="Photo of an accountant at a desk using a calculator" style="background:linear-gradient(170deg,#f2f3f5,#d7dce2 60%,#9aa1aa)"></div>
      <h3>ACCOUNTING SUPPORT</h3>
      <p>It is a long established fact that a reader will be distracted by the readable content of a page when looking at its layout. The point of using Lorem</p>
      <div class="service-rule"></div>
    </article>
    <article class="service">
      <div class="service-photo" role="img" aria-label="Photo of an advisor explaining figures to clients in a meeting" style="background:linear-gradient(150deg,#c8b79c,#eceae6 45%,#cfd6dc 75%,#6f7377)"></div>
      <h3>BUSINESS ADVICE</h3>
      <p>It is a long established fact that a reader will be distracted by the readable content of a page when looking at its layout. The point of using Lorem</p>
      <div class="service-rule"></div>
    </article>
  </section>

  <footer class="site-footer">
    <div class="social"><span></span><span></span><span></span><span></span><span></span><span></span><span></span></div>
    <div class="copyright">Copyrights@2016 Company name , All rights Reserved</div>
  </footer>
</body>
</html>
```